Business Card Design (NEW FILES)

ATTENTION: New vector files are available. Please update your design to reflect/use the new (better resolution) logo images.

Seeking a unique and professional business card design for a commercial drone photography/videography business. The layout should feature
the logo (attached) and include the following information:
Owen Tarrick
614-502-7738
www.skylarkreelworks.example
NRD Certified Remote Pilot

Owen Tarrick

```html
<!DOCTYPE html>
<html lang="en">
<head>
<meta charset="utf-8">
<title>Skylark Reelworks – Business Card</title>
<link rel="stylesheet" href="https://fonts.googleapis.com/css2?family=Roboto:wght@400;500;700&display=swap">
<style>
  :root {
    --navy: #151a48;
    --navy-tint: #2a3068;
    --navy-pale: #e3e5ef;
    --orange: #ef8a52;
    --white: #ffffff;
    --backdrop: #e9e9e9;
    --ink: #151a48;
  }
  * { margin: 0; padding: 0; box-sizing: border-box; }
  html, body {
    width: 1200px; height: 954px; overflow: hidden;
    background: var(--backdrop);
    font-family: "Roboto", Arial, sans-serif;
  }
  .canvas { position: relative; width: 1200px; height: 954px; }
  .card {
    position: absolute; top: 344px;
    width: 525px; height: 300px; overflow: hidden;
  }
  .card--front { left: 68px; background: var(--white); }
  .card--back { left: 606px; background: var(--navy); }

  .drone-art { position: absolute; }
  .card--front .drone-art {
    left: 125px; top: 6px; width: 400px; height: 294px;
    background: var(--navy-pale);
    border-radius: 120px 0 0 0;
  }
  .card--back .drone-art {
    left: 0; top: 6px; width: 400px; height: 150px;
    background: var(--navy-tint);
    border-radius: 0 0 160px 0;
  }

  .name-block { position: absolute; left: 0; top: 175px; }
  .name-block__bar {
    position: absolute; left: 0; top: 0;
    width: 17px; height: 36px; background: var(--orange);
  }
  .name-block__name {
    position: absolute; left: 28px; top: 0; white-space: nowrap;
    font-size: 18px; font-weight: 700; color: var(--ink); line-height: 20px;
  }
  .name-block__name .surname { color: var(--orange); }
  .name-block__role {
    position: absolute; left: 28px; top: 21px;
    font-size: 13px; color: var(--ink); line-height: 15px;
  }

  .contact {
    position: absolute; left: 28px; top: 233px;
    list-style: none; font-size: 14px; color: var(--ink);
  }
  .contact li { display: flex; align-items: center; height: 21px; white-space: nowrap; }
  .contact svg { width: 11px; height: 11px; margin-right: 8px; flex: none; }

  .divider {
    position: absolute; left: 254px; top: 236px;
    width: 1.5px; height: 36px; background: var(--ink);
  }
  .credentials {
    position: absolute; left: 268px; top: 233px;
    list-style: none; font-size: 14px; color: var(--ink);
  }
  .credentials li { height: 21px; line-height: 21px; white-space: nowrap; }

  .brand {
    position: absolute; left: 212px; top: 180px;
    display: flex; align-items: center; gap: 12px;
  }
  .brand__dot {
    width: 22px; height: 22px; border-radius: 50%; background: var(--orange); flex: none;
  }
  .brand__name {
    font-size: 28px; font-weight: 400; color: var(--white);
    line-height: 30px; letter-spacing: 0.5px;
  }
</style>
</head>
<body>
<main class="canvas">
  <section class="card card--front">
    <div class="drone-art" role="img" aria-label="Drone illustration with camera aperture, spanning the top of the card"></div>

    <div class="name-block">
      <span class="name-block__bar"></span>
      <p class="name-block__name">OWEN <span class="surname">TARRICK</span></p>
      <p class="name-block__role">Owner</p>
    </div>

    <ul class="contact">
      <li>
        <svg viewBox="0 0 12 12" aria-hidden="true"><path d="M2.5 1 L4.5 1 L5.3 3.4 L4 4.4 Q5 6.8 7.6 8 L8.6 6.7 L11 7.5 L11 9.5 Q10.5 11 9 11 Q1 10 1 2.5 Q1 1 2.5 1 Z" fill="var(--orange)"/></svg>
        614-502-7738
      </li>
      <li>
        <svg viewBox="0 0 12 12" aria-hidden="true"><g fill="none" stroke="var(--orange)" stroke-width="1.1"><circle cx="6" cy="6" r="5"/><ellipse cx="6" cy="6" rx="2.2" ry="5"/><path d="M1 6 H11 M2 3.5 H10 M2 8.5 H10"/></g></svg>
        www.skylarkreelworks.example
      </li>
    </ul>

    <span class="divider"></span>
    <ul class="credentials">
      <li>NRD Certified Remote Pilot</li>
      <li>Fully Insured</li>
    </ul>
  </section>

  <section class="card card--back">
    <div class="drone-art" role="img" aria-label="Drone illustration continuing across the top of the card"></div>
    <div class="brand">
      <span class="brand__dot"></span>
      <p class="brand__name">SKYLARK<br>REELWORKS</p>
    </div>
  </section>
</main>
</body>
</html>
```